New Bicycle shop business card

Hi!
I'm looking for a business card for my new proffesional bike mechanics shop. This shop is only for fixing broken bikes and not selling bikes.
Peferbly a modern and sleek and modern design.
Colors: black, grey, red, white
Information:
Name: Rijwielwerkplaats Vanhoutte
Shop owner: Bart Vanhoutte & Marieke Segers
Website: www.rijwielwerkplaats-vanhoutte.be
Email: info@rijwielwerkplaats-vanhoutte.be
Phone number: +32471902368
Street adres: Kerkweg 46
9940 Bellebeke
Slogan/shop information: Herstellingen van alle merken.
Logo: see files.
Target Market(s)
People who seek a mechanic to fix or upgrade their bikes.
Contact Information for Business Card
Information:
Website: info@rijwielwerkplaats-vanhoutte.be
9940 Bellebeke
Logo: see files.

```html
<!DOCTYPE html>
<html lang="nl">
<head>
<meta charset="utf-8">
<title>Rijwielwerkplaats Vanhoutte – Visitekaartjes</title>
<link rel="stylesheet" href="https://fonts.googleapis.com/css2?family=Roboto:wght@400;500;700&display=swap">
<style>
  :root {
    --stage: #e3e3e3;
    --card: #fbfbfb;
    --red: #d42a3c;
    --black: #1b1b1b;
    --grey: #9c9fa3;
    --white: #ffffff;
  }
  * { margin: 0; padding: 0; box-sizing: border-box; }
  html, body {
    width: 1200px; height: 852px; overflow: hidden;
    background: var(--stage);
    font-family: "Roboto", Arial, sans-serif;
  }
  .stage {
    width: 1200px; height: 852px;
    display: flex; align-items: center; justify-content: center; gap: 60px;
  }
  .card {
    position: relative;
    width: 520px; height: 300px;
    border-radius: 22px;
    background: var(--card);
    overflow: hidden;
    box-shadow: 0 4px 14px rgba(0,0,0,.12);
  }
  .card__art { position: absolute; inset: 0; width: 100%; height: 100%; }

  /* Front */
  .front__brand {
    position: absolute; left: 0; right: 0; top: 92px;
    display: flex; flex-direction: column; align-items: center; gap: 14px;
  }
  .brand-mark {
    width: 46px; height: 46px; border-radius: 50%;
    background: var(--red);
  }
  .brand-name {
    font-weight: 700; color: var(--black);
    text-transform: uppercase; letter-spacing: 2px;
    font-size: 22px; line-height: 1.15; text-align: center;
  }
  .front__slogan {
    position: absolute; left: 0; right: 0; top: 222px;
    display: flex; align-items: center; justify-content: center; gap: 14px;
    font-size: 13px; color: var(--black);
  }
  .front__slogan::before, .front__slogan::after {
    content: ""; width: 46px; height: 2px; background: var(--red);
  }

  /* Back */
  .back__brand {
    position: absolute; left: 26px; top: 30px;
    font-size: 19px; text-align: left;
  }
  .back__person {
    position: absolute; left: 26px; top: 120px; color: var(--white);
  }
  .person-name {
    font-weight: 700; font-size: 18px; line-height: 22px;
    letter-spacing: 1px; text-transform: uppercase;
  }
  .person-role { font-size: 11px; line-height: 13px; margin-top: 1px; opacity: .9; }
  .contact-list {
    list-style: none; margin-top: 8px;
    font-size: 12.5px; line-height: 19px;
  }
  .contact-list li { display: flex; align-items: center; gap: 9px; white-space: nowrap; }
  .contact-list svg { width: 12px; height: 12px; flex: none; fill: var(--white); }
  .back__slogan {
    position: absolute; left: 26px; bottom: 14px;
    font-size: 13px; color: var(--black);
  }
</style>
</head>
<body>
<main class="stage">

  <!-- Card front -->
  <section class="card card--front" aria-label="Voorkant visitekaartje">
    <svg class="card__art" viewBox="0 0 520 300" preserveAspectRatio="none" aria-hidden="true">
      <polygon points="0,286 190,286 200,300 0,300" fill="var(--red)"/>
      <polygon points="270,282 520,282 520,300 282,300" fill="var(--grey)"/>
    </svg>
    <div class="front__brand">
      <span class="brand-mark" aria-hidden="true"></span>
      <p class="brand-name">Rijwielwerkplaats<br>Vanhoutte</p>
    </div>
    <p class="front__slogan">Herstellingen van alle merken</p>
  </section>

  <!-- Card back -->
  <section class="card card--back" aria-label="Achterkant visitekaartje">
    <svg class="card__art" viewBox="0 0 520 300" preserveAspectRatio="none" aria-hidden="true">
      <polygon points="0,108 252,108 300,0 520,0 520,262 0,262" fill="var(--red)"/>
      <polygon points="282,0 304,0 256,108 234,108" fill="var(--white)"/>
      <circle cx="412" cy="108" r="72" fill="var(--white)"/>
    </svg>
    <p class="brand-name back__brand">Rijwielwerkplaats<br>Vanhoutte</p>
    <div class="back__person">
      <p class="person-name">Marieke Segers</p>
      <p class="person-role">Owner</p>
      <ul class="contact-list">
        <li>
          <svg viewBox="0 0 24 24" aria-hidden="true"><path d="M6.6 10.8a15.1 15.1 0 0 0 6.6 6.6l2.2-2.2a1 1 0 0 1 1-.25 11.4 11.4 0 0 0 3.6.57 1 1 0 0 1 1 1V20a1 1 0 0 1-1 1A17 17 0 0 1 3 4a1 1 0 0 1 1-1h3.5a1 1 0 0 1 1 1c0 1.25.2 2.45.57 3.57a1 1 0 0 1-.25 1z"/></svg>
          +32471902368
        </li>
        <li>
          <svg viewBox="0 0 24 24" aria-hidden="true"><path d="M12 2a10 10 0 1 0 0 20 10 10 0 0 0 0-20zm6.9 6h-2.9a15.6 15.6 0 0 0-1.4-3.6A8 8 0 0 1 18.9 8zM12 4a14 14 0 0 1 1.9 4h-3.8A14 14 0 0 1 12 4zM4.3 14a8 8 0 0 1 0-4h3.4a16.5 16.5 0 0 0 0 4zm.8 2h2.9a15.6 15.6 0 0 0 1.4 3.6A8 8 0 0 1 5.1 16zM8 8H5.1a8 8 0 0 1 4.3-3.6A15.6 15.6 0 0 0 8 8zm4 12a14 14 0 0 1-1.9-4h3.8A14 14 0 0 1 12 20zm2.3-6H9.7a14.7 14.7 0 0 1 0-4h4.6a14.7 14.7 0 0 1 0 4zm.3 5.6a15.6 15.6 0 0 0 1.4-3.6h2.9a8 8 0 0 1-4.3 3.6zm1.7-5.6a16.5 16.5 0 0 0 0-4h3.4a8 8 0 0 1 0 4z"/></svg>
          www.rijwielwerkplaats-vanhoutte.be
        </li>
        <li>
          <svg viewBox="0 0 24 24" aria-hidden="true"><path d="M2 5h20v14H2zm2 2v.5l8 5 8-5V7zm0 2.8V17h16V9.8l-8 5z"/></svg>
          info@rijwielwerkplaats-vanhoutte.be
        </li>
        <li>
          <svg viewBox="0 0 24 24" aria-hidden="true"><path d="M12 2a7 7 0 0 0-7 7c0 5.2 7 13 7 13s7-7.8 7-13a7 7 0 0 0-7-7zm0 9.5A2.5 2.5 0 1 1 12 6.5a2.5 2.5 0 0 1 0 5z"/></svg>
          Kerkweg 46 9940 Bellebeke
        </li>
      </ul>
    </div>
    <p class="back__slogan">Herstellingen van alle merken</p>
  </section>

</main>
</body>
</html>
```